MRT Property - Business Cards

Looking for a business card & general letterhead, signage etc design for our new logo.

Colours:
000a20
0056a2
00b5ef
0088ce
68cef2

Fonts:
Poppins
Karla

Please keep look and feel of new brand - example in the zip package I sent.

```html
<!DOCTYPE html>
<html lang="en">
<head>
<meta charset="utf-8">
<title>MRT Property – Business Cards</title>
<link rel="stylesheet" href="https://fonts.googleapis.com/css2?family=Montserrat:wght@400;500;600;700&display=swap">
<style>
  :root{
    --ink:#000a20;
    --navy-card:#0f1428;
    --brand-blue:#0056a2;
    --mid-blue:#0088ce;
    --bright-blue:#00b5ef;
    --pale-blue:#68cef2;
    --text-dark:#1c1c1c;
    --paper:#ffffff;
    --backdrop:#e6e5e7;
  }
  *{margin:0;padding:0;box-sizing:border-box;}
  html,body{width:1200px;height:1108px;overflow:hidden;background:var(--backdrop);}
  body{position:relative;font-family:"Montserrat",sans-serif;}

  .card{position:absolute;left:233px;width:771px;height:440px;}
  .card--front{top:67px;background:var(--paper);}
  .card--back{top:581px;background:var(--navy-card);}

  .wordmark{position:absolute;display:flex;align-items:center;font-family:"Montserrat",sans-serif;font-weight:700;color:var(--brand-blue);white-space:nowrap;}
  .wordmark__dot{border-radius:50%;background:var(--mid-blue);flex:none;}
  .card--front .wordmark{right:24px;top:88px;font-size:46px;gap:16px;}
  .card--front .wordmark__dot{width:54px;height:54px;}
  .card--back .wordmark{left:50%;top:50%;transform:translate(-50%,-50%);font-size:72px;gap:26px;}
  .card--back .wordmark__dot{width:86px;height:86px;}

  .person{position:absolute;left:38px;top:234px;}
  .person__name{font-weight:700;font-size:29px;color:var(--brand-blue);letter-spacing:.3px;line-height:1;}
  .person__role{margin-top:12px;font-weight:400;font-size:20px;color:var(--text-dark);letter-spacing:.4px;}

  .divider{position:absolute;left:38px;right:40px;top:317px;height:2px;background:var(--text-dark);}

  .contacts{position:absolute;left:36px;top:332px;list-style:none;}
  .contacts li{display:flex;align-items:center;gap:14px;height:30px;font-size:20px;color:var(--text-dark);}
  .contacts svg{width:22px;height:22px;flex:none;fill:none;stroke:var(--mid-blue);stroke-width:2;}

  .address{position:absolute;right:34px;top:362px;text-align:right;font-size:20px;line-height:30px;color:var(--text-dark);font-style:normal;}
</style>
</head>
<body>

<section class="card card--front" aria-label="Business card front">
  <div class="wordmark"><span class="wordmark__dot"></span>MRT Property</div>

  <div class="person">
    <h1 class="person__name">DANIEL HARPER</h1>
    <p class="person__role">MANAGING DIRECTOR</p>
  </div>

  <div class="divider"></div>

  <ul class="contacts">
    <li>
      <svg viewBox="0 0 24 24" aria-hidden="true"><path d="M5 3l4 1 1 5-2 1.5a12 12 0 0 0 5.5 5.5L15 14l5 1 1 4-2 2C11 21 3 13 3 5z" fill="var(--mid-blue)" stroke="none"/><path d="M14 4a7 7 0 0 1 6 6M14 8a3 3 0 0 1 2 2"/></svg>
      044-987 654 321
    </li>
    <li>
      <svg viewBox="0 0 24 24" aria-hidden="true"><rect x="3" y="6" width="18" height="13" fill="var(--mid-blue)" stroke="none"/><path d="M3 6l9 7 9-7M3 19l7-6M21 19l-7-6" stroke="#fff" stroke-width="1.5"/></svg>
      hello@mrtproperty.com
    </li>
    <li>
      <svg viewBox="0 0 24 24" aria-hidden="true"><circle cx="12" cy="12" r="9"/><ellipse cx="12" cy="12" rx="4" ry="9"/><path d="M3 12h18M5 7h14M5 17h14"/></svg>
      www.mrtproperty.com
    </li>
  </ul>

  <address class="address">421, Address line goes here<br>45452, Country name</address>
</section>

<section class="card card--back" aria-label="Business card back">
  <div class="wordmark"><span class="wordmark__dot"></span>MRT Property</div>
</section>

</body>
</html>
```